2022 Yearly Patron Drive (art gallery annual report)

6X9, 16-page brochure that serves both as an annual report for the previous year and gets mailed for an ask for donations. This must be done in InDesign and I will provide a template. I am also sending PDFs for the previous two years. Last year was pink and black, but I have recolored the logo purple this year.. so am open to whatever colors. I used last year's template to put in the new info. The theme for this year is Amazing - last year was Thriving. The font I chose for the front I do not want to use.. its just an example. All three pictures on the front don't have to be used.. just ideas.
Updates

I put three photos on the front page. It isn't necessary to use all of them, I thought there might be something there to use as part of the design

The current information is in the InDesign file, Calatalog Design.indd with the to Links Folders attached.

Target Market(s)

Donors

Industry/Entity Type

Art

Font styles to use
Sans Serif

Requirements
Must have
• InDesign
Nice to have
• A new look! Something different than 2021 an 2020 (PDFs included)

```html
<!DOCTYPE html>
<html lang="en">
<head>
<meta charset="utf-8">
<title>Annual Gifts – Yearly Patron Drive</title>
<link href="https://fonts.googleapis.com/css2?family=Bebas+Neue&family=Open+Sans:ital,wght@0,400;0,700;1,700&family=Playfair+Display:wght@500&display=swap" rel="stylesheet">
<style>
  :root {
    --ink: #231f20;
    --text: #2b2b2b;
    --orange: #f37a2f;
    --pink: #e8449a;
    --magenta: #c42a8e;
    --plum: #7b2d45;
    --slate: #3a3340;
    --paper: #ffffff;
    --rule: #3a3a3a;
  }
  * { margin: 0; padding: 0; box-sizing: border-box; }
  html, body { width: 1200px; height: 800px; overflow: hidden; background: var(--paper); }
  .page { position: relative; width: 1200px; height: 800px; font-family: "Open Sans", Arial, sans-serif; color: var(--text); }

  .brand {
    position: absolute; left: 54px; top: 52px;
    font-family: "Open Sans", Arial, sans-serif; font-weight: 700;
    font-size: 26px; letter-spacing: 1.5px; color: var(--ink); line-height: 1;
  }

  .thanks {
    position: absolute; left: 600px; top: 106px;
    font-weight: 700; font-size: 19.5px; line-height: 24px; color: var(--pink);
  }
  .thanks em { font-style: italic; }

  .section-title {
    position: absolute; left: 112px; top: 146px;
    font-family: "Bebas Neue", Impact, sans-serif; font-weight: 400;
    font-size: 66px; line-height: 1; color: var(--orange); letter-spacing: 0.5px;
  }

  .donor-list {
    position: absolute; left: 113px; top: 218px; width: 1020px;
    font-size: 16.2px; line-height: 22.3px; text-align: justify; color: var(--text);
  }
  .donor-list .feature-space { float: right; width: 284px; height: 200px; }
  .sep { color: var(--orange); }

  .feature { position: absolute; left: 874px; top: 258px; width: 226px; height: 130px; }
  .feature .accent-block { position: absolute; left: 0; top: 80px; width: 46px; height: 48px; background: var(--magenta); }
  .feature .gallery-photo {
    position: absolute; left: 46px; top: 14px; width: 168px; height: 114px;
    background: linear-gradient(180deg, #5a5652 0%, #cfcac2 38%, #e4e0da 62%, #4a4744 100%);
  }
  .feature .dark-block { position: absolute; left: 203px; top: 3px; width: 22px; height: 22px; background: var(--ink); }

  .page-footer { position: absolute; left: 0; top: 738px; width: 1200px; height: 30px; }
  .page-number {
    position: absolute; left: 0; top: 1px; width: 55px; height: 25px;
    background: var(--slate); border-radius: 0 13px 13px 0;
    color: #fff; font-weight: 700; font-size: 14px; line-height: 25px; padding-left: 28px;
  }
  .theme-word {
    position: absolute; left: 67px; top: -4px;
    font-family: "Playfair Display", Georgia, serif; font-weight: 500;
    font-size: 25px; color: var(--plum); line-height: 1.2;
  }
  .footer-rule { position: absolute; left: 189px; top: 15px; width: 1011px; height: 1px; background: var(--rule); }
</style>
</head>
<body>
<div class="page">
  <div class="brand">HALVERN</div>

  <p class="thanks">Thank you to all our donors who gave to our<br>eighth <em>Yearly Patron Drive</em> campaign a total of $26,905</p>

  <h1 class="section-title">ANNUAL GIFTS</h1>

  <div class="feature">
    <div class="accent-block"></div>
    <div class="gallery-photo" role="img" aria-label="Gallery interior with framed artworks on white walls and sculptures on white plinths"></div>
    <div class="dark-block"></div>
  </div>

  <p class="donor-list"><span class="feature-space"></span>Nora Ashcombe <span class="sep">•</span> Jodie Arlen <span class="sep">•</span> Ivo &amp; Clara Aldous <span class="sep">•</span> Evan &amp; Chandler Andrews <span class="sep">•</span> Delia Rann <span class="sep">•</span> Corinne &amp; Martin Bardwell <span class="sep">•</span> Joel Baxley <span class="sep">•</span> Marlene Blanchet <span class="sep">•</span> Jake &amp; Connie Broxton <span class="sep">•</span> Neil Walden &amp; Anne Bowden <span class="sep">•</span> Timothy Brannock <span class="sep">•</span> Sherry &amp; Mick Brookdale <span class="sep">•</span> Lydia C Browne <span class="sep">•</span> Dolores Carrera-Fell <span class="sep">•</span> Russell Mayer &amp; Sara Coyle <span class="sep">•</span> Beatrix Cole <span class="sep">•</span> Margaret Copley <span class="sep">•</span> Debra Cornell <span class="sep">•</span> Jim &amp; Gail Dawes <span class="sep">•</span> Carol-Anne de La Rochelle <span class="sep">•</span> Dennis Dunmore <span class="sep">•</span> Sonja Dorsey <span class="sep">•</span> Dena &amp; Dave Ellery <span class="sep">•</span> Doug Lennox &amp; Susan Eriksen <span class="sep">•</span> Jim Finch <span class="sep">•</span> Steve &amp; Priscilla Fordham <span class="sep">•</span> W D Franklin <span class="sep">•</span> Craig &amp; Barbara Smythe Gilmore <span class="sep">•</span> Marlena &amp; Bruce Gillam <span class="sep">•</span> Karl &amp; Mary Grant <span class="sep">•</span> Jane Granger <span class="sep">•</span> Victor Lorca &amp; Susan Hale <span class="sep">•</span> Norma Harley <span class="sep">•</span> Tom &amp; Cherie Hansford <span class="sep">•</span> James &amp; Jacqueline Hartley <span class="sep">•</span> Mary Holloway <span class="sep">•</span> Hilde Hibbert <span class="sep">•</span> Mike &amp; Kristin Hilden <span class="sep">•</span> Don Hinshaw <span class="sep">•</span> Virginia Hollis <span class="sep">•</span> Eric &amp; Lauren Holman <span class="sep">•</span> Renee Holzinger <span class="sep">•</span> Kasper &amp; Mary Hovanian <span class="sep">•</span> Jan Moravec &amp; Stan Hurley <span class="sep">•</span> Robert Colby &amp; Judy Hurlbut <span class="sep">•</span> Linda Iacono <span class="sep">•</span> Karen Irvine MD <span class="sep">•</span> Dave &amp; Meg Ingram <span class="sep">•</span> Jerry Jansen <span class="sep">•</span> Kay &amp; Royal Keeler <span class="sep">•</span> Patrick &amp; Pamela Kendrick <span class="sep">•</span> Curtis Kingsley <span class="sep">•</span> James &amp; Linda Kurtz <span class="sep">•</span> Beverly Lane <span class="sep">•</span> Roger Sievert &amp; Linda Lawfield <span class="sep">•</span> Peggy Lowell <span class="sep">•</span> Judith Lorimer <span class="sep">•</span> David Lyle <span class="sep">•</span> Neal &amp; Leslie McCrory <span class="sep">•</span> Saundra McPhail <span class="sep">•</span> Elizabeth and Carter Milner <span class="sep">•</span> Marilyn Minton <span class="sep">•</span> Thomas &amp; Anne Mortensen <span class="sep">•</span> Marji Morley <span class="sep">•</span> Stephen &amp; Laura Muellner <span class="sep">•</span> Carolyn Nesbitt <span class="sep">•</span> Cheryl LaFleur &amp; Richard Novak <span class="sep">•</span> Jane Orloff <span class="sep">•</span> Deane &amp; Marilyn Paley <span class="sep">•</span> Ty Preston <span class="sep">•</span> Marj Petrie <span class="sep">•</span> Linda Pike <span class="sep">•</span> Sue Reid <span class="sep">•</span> Linda Rusch <span class="sep">•</span> Al Fisher &amp; Charlie Rowan <span class="sep">•</span> Joyce Rothman <span class="sep">•</span> Nancy &amp; John Rossmann <span class="sep">•</span> Richard Rutledge Family • Paul &amp; Terri Schaefer <span class="sep">•</span> Paul &amp; Patty Shafter <span class="sep">•</span> Christian &amp; Janet Schleier <span class="sep">•</span> Larry &amp; Rebecca E Scholz <span class="sep">•</span> Denali Granberg &amp; Bruce Simmons <span class="sep">•</span> Ken &amp; Millie Stenberg <span class="sep">•</span> Lucy &amp; Jeff Stetson <span class="sep">•</span> Ed &amp; Lynn Stowell <span class="sep">•</span> Pat Sundberg <span class="sep">•</span> Joyce Swain <span class="sep">•</span> Susan, Jerry, Carter &amp; Christine Tolliver <span class="sep">•</span> Delma Tatum <span class="sep">•</span> Bette S Tyler <span class="sep">•</span> Brooke Cresswood &amp; TJ Tornberg <span class="sep">•</span> Joshua Trent <span class="sep">•</span> Jayne Tunney <span class="sep">•</span> Annemarie Van Leeuwen <span class="sep">•</span> George &amp; Mavis Velasquez <span class="sep">•</span> Cecilia &amp; Eric Voss <span class="sep">•</span> Robert &amp; Leslie Walsh <span class="sep">•</span> Wendy Warrick <span class="sep">•</span> Chuck &amp; Gloria Wendell <span class="sep">•</span> Dr. &amp; Mrs. Ulla Whitcombe <span class="sep">•</span> Dick &amp; Inga Wiebe <span class="sep">•</span> Ralph L Woodward <span class="sep">•</span> Jeffrey Schaaf &amp; Gilbert Yardley</p>

  <footer class="page-footer">
    <div class="page-number">14</div>
    <div class="theme-word">Amazing</div>
    <div class="footer-rule"></div>
  </footer>
</div>
</body>
</html>
```